Website front end design for an education nonprofit

This project involves design and development of the website front end (i.e., Web user interface and user experience design) for TAVO Sphere, a nonprofit initiative for developing an online platform for basic English language instruction, especially targeted toward underprivileged, non-native English speaking populations.

More about us: We are a team of educators, researchers and engineers passionate about this cause and would like to invite talented, creative web developers to join us in this effort to create positive social impact! Please send a personal message to the project owner for the executive summary to get more information about our initiative, big picture vision and the team.

TAVO Sphere website front end (UI/UX) design
Our key goals for this project are to develop an impressive Drupal-based front end for our website as well as to find really talented and creative web/UI/UX designers-cum-developers who are experts in the state-of-the-art web technologies, and are passionate about the cause of global online basic education. At the end of this project, we hope to have long term engagement with the selected developer(s) for our future website design and development needs.

Here are some preliminary guidelines on the TAVO Sphere website front end framework as envisioned by us so far. Please note that we would very much encourage creative ideas and mock-ups from the developers.

1. Current platform: Our website prototype back-end uses Drupal CMS (we plan to continue using Drupal CMS) and at the moment, a toy front-end is based on the Drupal Skeleton platform for its simplicity, clean UI and mobile device friendliness. The web developer / designer can choose any Drupal front end as a starting point or come up with a new Drupal template that meets our requirements below. Prior experience and expertise on Drupal would be great.

2. Audience profile: While the primary audience for the website is expected to be young kids (6-10 years) not very familiar with English, the secondary audience also includes adults interested in basic English language skills. So the overall goal is to have simple, uncluttered / clean, elegant and lightweight (think loading time as well as mobile device friendliness) interface that is extremely intuitive and easy to navigate, is artistic and aesthetically appealing to a wide audience (especially the non-native English speaking populations). The most important point is that our target audience should feel welcome with the clean, crisp look and easy, user-centric navigation, and should in no case feel overwhelmed (say with too much text or clutter on the front page).

3. Front page: Here is a currently envisioned preliminary sketch of the website front page (very much open for refinement and improvements)
a. The top “menu bar” part of the landing page will have our organization name and logo along with (or above) the top menu bar with the following links and sub-links
i. “Learn” link with sub-menu of all our content sections (World learning, Basic sentence learning, Classic short stories, Picture Dictionary)
ii. “About” links with information about us (sub-menu entries: About TAVO Sphere, Team, Supporters, Contributors)
iii. “Contribute” link with sub-menu entries Donate, Volunteer
iv. Menu entries towards the right side: “Login / sign up” followed by
v. “Search” with space to enter the search phrase
b. The middle “main page content” part of the page is where we would have entry points to our main content categories. The portion is envisioned to be graphical, with big blocks (images) as links to our content categories. The current categories (to start with) include 1. Word learning, 2. Basic sentence learning, and 3. Classic stories. We welcome creative ideas to represent these content categories in an appealing and elegant way (for example, these content categories could be portrayed as closed double doors that lead to the pages with the content. We would like to have placeholders for appropriate image links to different content categories – we should be able to put appropriate images or change them as we come up with new ideas that would work best with our target audience). The categories would change and grow as our content evolves, hence the core idea is to build a flexible framework that readily allows for expansion as well as customization.
c. The bottom menu / links bar portion of the landing page will have a list of links that are not included at the top. Examples include (with flexibility needed to add more when needed)
i. “Help”: this leads to a new page with FAQ, How to use
ii. “Contact us” link to a web contact form page
iii. “For Teachers” link to a page with information such as how to use, tips, pilot programs,
iv. “Volunteer” link to page with links such as Donate, Volunteer
v. “Contributors” that would link to a page with information about our Artists, Teachers, Writers, Developers etc.
vi. “Jobs” would link to a jobs page
vii. “Blog” would lead to our blog page
viii. “User stories” link to pages with feedback that we obtain from the users about how the content has helped them,
ix. Web 2.0 placeholders for social media (to be added later)

d. The footer of the website should include text “2013 TAVO Sphere, All rights reserved.”

4. The middle block of the front page is the largest in screen real estate and perhaps the most challenging part that requires much creativity and thought on the UI/UX design aspect – the content pages pointed to by the section links on the middle portion of the front page are also being designed.

5. Color preference is towards soft, elegant (think grays, whites, light blues, other light colors) web safe colors. No harsh (too bright, garish) colors.

6. Fonts preference Nice, clean looking fonts (Arial alright) compatible across browsers.

7. Portability and robustness of the front page layout for different platforms should be carefully considered. Although our first launch target platform is PC (where cross browser compatibility is important), this would very soon be followed by mobile devices such as tablets and smartphones given their prevalence across the globe. This mobile friendly design or easy portability to mobile platforms with little work requirement should be considered as a design requirement.

8. Front page as a framework for the complete website: Note that the top and the bottom portions of the front page are envisioned be used as a common template / frame across all the pages of our website – the middle portion would be used to show our content on the other pages of our website.

9. UX: For the UI/UX design, it is critical to keep in mind key qualities such as ease of use, simplicity, elegance and artistic appeal. Some specific points to keep in mind: (1) the major portion of the target audience would be new to English and (2) young children are expected to be the primary audience but we want the website to appeal to adults interested in learning as well, and (3) we need the website to work even with relatively slow Internet speeds (for underdeveloped / developing regions especially), should always be kept in mind. HTML5 compliance ideas are encouraged.

10. Strictly not desired: Typical corporate feel seen in many webpages, blocky graphics, dull and uninviting overall look with no personality, Flash type effects, harsh colors.

11. Creativity and imagination necessary: We would like to reiterate that the designer/developer has complete freedom to re-imagine the front page considering the above requirements and get back with ideas for an inspiring layout that presents the content outlined above in an intuitive format, carefully considering our target audience.

A note: As a rule, we will always make sure that our developers and artists get proper credit for their work and are recognized and acknowledged by everyone visiting our website.

Expected deliverables:
Website design psd files AND coded webpage / Drupal template: the corresponding source code and all the required libraries, images etc would be required with minimal documentation / pointers on how to make changes and customizations.

Interested developers are encouraged to first send us preliminary prototype Design for the front page to get feedback on whether their approach and style is in line with our needs and preferences. We will suggest the developers to proceed further if the team thinks there is some potential for a match (of course, the final determination would be from the pool of shortlisted submissions) – otherwise, in case the team does not see potential for a match with our needs or if we have already received multiple submissions that are comparatively more closely aligned with our vision for the website, we'd prefer to be respectful of the developers’ time and effort by requesting them not to proceed further.

Please consider this effort as your contribution to an important social cause of global and accessible online education and not a commercial enterprise (our passion for making a positive impact is what is driving the TAVO Sphere nonprofit team to undertake this initiative!). We would like to invite you to join us in this effort!

Project Deadline Extended
Reason: Due to requests from interested designers, we are extending the deadline. Looking forward to receiving many other creative designs!

Please see the project brief.

Real Estate

• Please see the project brief.

```html
<!DOCTYPE html>
<html lang="en">
<head>
<meta charset="utf-8">
<title>TAVO Sphere – Learn English</title>
<link rel="stylesheet" href="https://fonts.googleapis.com/css2?family=Open+Sans:wght@400;600;700;800&display=swap">
<style>
:root{
  --ink:#333a40;
  --muted:#7c858c;
  --accent:#2d9fd3;
  --accent-soft:#a8dbef;
  --accent-pale:#d9eef7;
  --dark:#3b4146;
  --hero-top:#e9edf0;
  --hero-bottom:#fbfcfc;
  --footer:#eceff1;
  --line:#dde3e7;
  --white:#ffffff;
}
*{box-sizing:border-box;margin:0;padding:0}
html,body{width:896px;height:1200px;overflow:hidden}
body{font-family:"Open Sans",Arial,sans-serif;color:var(--ink);background:var(--white);font-size:10px;line-height:1.5}
.wrap{width:630px;margin:0 auto;position:relative}

/* header */
.site-header{height:58px;display:flex;align-items:center;padding:0 26px 0 28px;border-bottom:1px solid var(--line)}
.brand{font-size:24px;font-weight:800;color:var(--dark);letter-spacing:-.3px;width:310px}
.main-nav{display:flex;gap:4px;font-size:10px;font-weight:600}
.main-nav a{color:var(--ink);text-decoration:none;padding:4px 9px}
.main-nav a.active{background:var(--accent-pale);border:1px solid var(--accent-soft);border-radius:2px}
.search{margin-left:22px;width:72px;height:18px;border:1px solid #c6ccd0;border-radius:9px;background:var(--white);display:flex;align-items:center;justify-content:flex-end;padding-right:5px}
.account{margin-left:auto;display:flex;gap:4px}
.account a{background:var(--dark);color:var(--white);font-size:9px;text-decoration:none;padding:4px 12px;border-radius:2px}

/* hero */
.hero{height:334px;background:linear-gradient(var(--hero-top),var(--hero-bottom));position:relative}
.hero-copy{position:absolute;left:120px;top:78px;width:230px}
.hero-copy h1{font-size:11px;font-weight:800;color:var(--dark);margin-bottom:6px}
.hero-copy p{font-size:9px;color:var(--muted);margin-bottom:18px}
.btn{display:inline-block;background:var(--accent-soft);color:var(--dark);font-weight:700;font-size:8px;text-decoration:none;padding:4px 14px;border-radius:2px}
.hero-copy .btn{padding:7px 26px}
.hero-art{position:absolute;left:420px;top:40px;width:370px;height:240px;background:radial-gradient(ellipse at 45% 45%,#e25b4e 0,#b8352c 45%,var(--hero-top) 72%);border-radius:6px}
.hero-arrow{position:absolute;top:200px;width:20px;height:30px;background:#c9cfd3;border-radius:2px;display:flex;align-items:center;justify-content:center}
.hero-arrow.prev{left:34px}.hero-arrow.next{right:34px}

/* welcome */
.welcome{display:flex;gap:30px;padding:30px 0 22px;border-bottom:1px solid var(--line)}
.welcome-photo{width:118px;height:118px;border-radius:50%;background:linear-gradient(135deg,#c8a08a,#8d6b5b);flex:none;border:4px solid var(--white);box-shadow:0 0 0 1px var(--line)}
.welcome h2{font-size:17px;font-weight:600;color:var(--accent);margin-top:4px}
.welcome h3{font-size:9px;font-weight:700;color:var(--dark);margin-bottom:6px}
.welcome p{font-size:9px;color:var(--muted)}
.more-link{display:block;text-align:right;font-size:8px;font-weight:700;color:var(--dark);margin-top:8px}

/* features */
.features{display:flex;gap:30px;padding:22px 0 20px;border-bottom:1px solid var(--line)}
.feature{width:190px}
.feature h2{font-size:15px;font-weight:600;color:var(--accent);margin-bottom:8px}
.feature-img{height:70px;border-radius:3px;margin-bottom:10px}
.feature p{font-size:8px;color:var(--muted);margin-bottom:10px}
.feature .btn{margin-left:122px}

/* blog + testimonials */
.stories{display:flex;gap:26px;padding:22px 0 14px}
.stories>section{flex:1}
.bar{background:var(--accent-soft);color:var(--white);font-size:13px;font-weight:600;padding:3px 16px;border-radius:2px;margin-bottom:10px}
.post{display:flex;gap:10px;margin-bottom:12px}
.thumb{width:40px;height:40px;border-radius:50%;flex:none}
.post h4{font-size:9px;font-weight:700;color:var(--dark)}
.post time{display:block;font-size:7px;color:var(--accent)}
.post p{font-size:8px;color:var(--muted)}
.quote{display:flex;gap:12px;margin-bottom:10px}
.quote .avatar{width:42px;height:42px;border-radius:3px;flex:none}
.quote blockquote{background:var(--accent-pale);border-radius:3px;padding:6px 10px;font-size:8px;color:var(--muted);position:relative;flex:1}
.quote cite{display:block;text-align:right;font-style:normal;font-size:11px;color:var(--dark);font-weight:600}
.more-row{text-align:right;font-size:8px;font-weight:700;color:var(--dark)}

/* footer */
.site-footer{position:absolute;left:0;top:1048px;width:896px;height:152px;background:var(--footer);border-top:1px solid var(--line)}
.footer-cols{display:flex;padding:16px 0 0 122px}
.footer-col h5{font-size:13px;font-weight:600;color:var(--dark);margin-bottom:6px}
.footer-col ul{list-style:none;font-size:7px;color:var(--muted);columns:2;column-gap:28px}
.footer-col li{margin-bottom:3px;padding-left:7px;position:relative}
.footer-col li::before{content:"";position:absolute;left:0;top:4px;width:3px;height:3px;background:var(--accent)}
.footer-col.quick{width:210px}
.footer-col.learn{width:170px}.footer-col.learn ul,.footer-col.about ul,.footer-col.give ul{columns:1}
.footer-col.about{width:130px}
.social{position:absolute;left:122px;top:112px;display:flex;gap:5px}
.social span{width:14px;height:14px;border-radius:2px;background:#9aa3a9}
.copyright{position:absolute;right:130px;top:128px;font-size:7px;color:var(--muted)}
</style>
</head>
<body>

<header class="site-header">
  <div class="brand">TAVO Sphere</div>
  <nav class="main-nav">
    <a class="active" href="#">Home</a><a href="#">Learn</a><a href="#">About</a><a href="#">Contribute</a>
  </nav>
  <div class="search">
    <svg width="9" height="9" viewBox="0 0 10 10"><circle cx="4" cy="4" r="3" fill="none" stroke="#5c666c" stroke-width="1.4"/><line x1="6.3" y1="6.3" x2="9.2" y2="9.2" stroke="#5c666c" stroke-width="1.4"/></svg>
  </div>
  <div class="account"><a href="#">Login</a><a href="#">SignUp</a></div>
</header>

<section class="hero">
  <div class="hero-copy">
    <h1>NON PROFIT ENGLISH LEARNING ONLINE PLATFORM</h1>
    <p>Simple lessons for every learner, at home or at school. Words, sentences and short stories, free for all, in plain English.</p>
    <a class="btn" href="#">MORE</a>
  </div>
  <div class="hero-art" role="img" aria-label="Large red 3D word LEARN with a computer mouse on a soft grey backdrop"></div>
  <div class="hero-arrow prev"><svg width="8" height="12" viewBox="0 0 8 12"><path d="M6 1 1 6l5 5" fill="none" stroke="#fff" stroke-width="2"/></svg></div>
  <div class="hero-arrow next"><svg width="8" height="12" viewBox="0 0 8 12"><path d="M2 1l5 5-5 5" fill="none" stroke="#fff" stroke-width="2"/></svg></div>
</section>

<main class="wrap">
  <section class="welcome">
    <div class="welcome-photo" role="img" aria-label="Photo of a child learning with a teacher"></div>
    <div>
      <h2>WELCOME TO TAVO SPHERE</h2>
      <h3>Mauris Vel Lacus Vitae Tellus Vestibulum Volutpat</h3>
      <p>We are educators, researchers and engineers building a free place to learn basic English. Our lessons are short, clear and friendly, made for children aged six to ten and for adults who are new to the language. Start with words, move on to sentences and enjoy classic stories.</p>
      <span class="more-link">» More</span>
    </div>
  </section>

  <section class="features">
    <article class="feature">
      <h2>For Teachers</h2>
      <div class="feature-img" role="img" aria-label="Photo of a teacher reading with pupils" style="background:linear-gradient(135deg,#d9c2b0,#9c7c68)"></div>
      <p>Guides, tips and pilot programs to help you bring our lessons into your classroom. Plan each week with ready made activities for young learners.</p>
      <a class="btn" href="#">More</a>
    </article>
    <article class="feature">
      <h2>Volunteer</h2>
      <div class="feature-img" role="img" aria-label="Colourful raised hands" style="background:linear-gradient(90deg,#e0463c,#f2b233,#55b04a,#3a8fd0)"></div>
      <p>Give a few hours each month to record audio, review lessons or help new students. Every hand makes our classes better for children everywhere.</p>
      <a class="btn" href="#">More</a>
    </article>
    <article class="feature">
      <h2>Contributors</h2>
      <div class="feature-img" role="img" aria-label="Hands joined together in a circle" style="background:linear-gradient(135deg,#e3d3c1,#a78a6f)"></div>
      <p>Meet the artists, writers, teachers and developers who shape our content. Their pictures, stories and code keep learning open and free for all.</p>
      <a class="btn" href="#">More</a>
    </article>
  </section>

  <div class="stories">
    <section>
      <div class="bar">Blog</div>
      <div class="post">
        <div class="thumb" role="img" aria-label="Blog post photo" style="background:linear-gradient(135deg,#c9b6a6,#87705f)"></div>
        <div><h4>Doloremque Rem Aperiam</h4><time>July 16, 2013</time><p>Five easy games that help children remember new words every day.</p></div>
      </div>
      <div class="post">
        <div class="thumb" role="img" aria-label="Blog post photo" style="background:linear-gradient(135deg,#b9c7d2,#6f8392)"></div>
        <div><h4>Doloremque Rem Aperiam</h4><time>July 16, 2013</time><p>How short stories build confidence in readers who are new to English.</p></div>
      </div>
      <div class="more-row">MORE ›</div>
    </section>
    <section>
      <div class="bar">Testimonials</div>
      <div class="quote">
        <div class="avatar" role="img" aria-label="Portrait of a parent" style="background:linear-gradient(135deg,#d3b29a,#94705a)"></div>
        <blockquote>My daughter now reads simple books on her own. The lessons are clear and fun.<cite>John</cite></blockquote>
      </div>
      <div class="quote">
        <div class="avatar" role="img" aria-label="Portrait of an adult learner" style="background:linear-gradient(135deg,#d8bfae,#9b7b66)"></div>
        <blockquote>I learned basic English at night after work. Thank you for making it free.<cite>Mary</cite></blockquote>
      </div>
      <div class="more-row">MORE ›</div>
    </section>
  </div>
</main>

<footer class="site-footer">
  <div class="footer-cols">
    <div class="footer-col quick">
      <h5>Quick Links</h5>
      <ul><li>Help</li><li>For Teachers</li><li>Volunteer</li><li>Contributors</li><li>Jobs</li><li>Blog</li><li>User Stories</li><li>Contact Us</li></ul>
    </div>
    <div class="footer-col learn">
      <h5>Learn</h5>
      <ul><li>Word Learning</li><li>Basic Sentence Learning</li><li>Classic Short Stories</li><li>Picture Dictionary</li></ul>
    </div>
    <div class="footer-col about">
      <h5>About</h5>
      <ul><li>About TAVO Sphere</li><li>Team</li><li>Supporters</li><li>Contributors</li></ul>
    </div>
    <div class="footer-col give">
      <h5>Contribute</h5>
      <ul><li>Donate</li><li>Volunteer</li></ul>
    </div>
  </div>
  <div class="social" aria-label="Social media placeholders"><span></span><span></span><span></span><span></span><span></span><span></span><span></span></div>
  <p class="copyright">© 2013 TAVO Sphere, All rights reserved.</p>
</footer>

</body>
</html>
```